Insurance Agency website design for Brellow Cover Insurance, LP

Build a website for Brellow Cover Insurance, LP which sells Homeowners, Auto, Renters, Condo, Flood, Disability, Life, Umbrella, and health insurance. We need the coolest insurance agency website out there to get quotes, contact us, or get additional information. Please list the following insurance companies we work with: Varnix, Ostle, Meridale Mutual, Quillor, Dunmarrow, KGZ, and Pellwick.

Make a design similar to https://www.fernagentry.com/

Selling personal insurance policies

```html
<!DOCTYPE html>
<html lang="en">
<head>
<meta charset="utf-8">
<title>Brellow Cover Insurance</title>
<link href="https://fonts.googleapis.com/css2?family=Montserrat:wght@400;500;600;700&display=swap" rel="stylesheet">
<style>
:root{
  --navy:#0d2f7d;
  --navy-deep:#0b3b8c;
  --green:#5aa626;
  --green-light:#8bc34a;
  --ink:#1d1d1d;
  --muted:#777;
  --bg-soft:#f1f2f4;
  --line:#d8dbe0;
  --white:#fff;
}
*{box-sizing:border-box;margin:0;padding:0}
html,body{width:1200px;height:4724px;overflow:hidden}
body{font-family:'Montserrat',sans-serif;color:var(--ink);background:var(--white);position:relative}
.abs{position:absolute}
section,header,footer{position:absolute;left:0;width:1200px}
.label{font-size:12px;font-weight:500;letter-spacing:1px;color:var(--green);text-transform:uppercase}
.title{font-size:28px;font-weight:700;color:var(--navy)}
.rule{width:64px;height:3px;background:var(--green)}
.center{text-align:center;left:0;width:1200px}
.btn{display:flex;align-items:center;justify-content:center;font-size:14px;font-weight:500;border-radius:3px;color:var(--white)}
.btn.navy{background:var(--navy)}
.btn.green{background:var(--green-light)}

/* header / hero */
.hero{top:0;height:630px;background:linear-gradient(90deg,#f3f4f6 0%,#e9ecef 45%,#dfe3e8 100%)}
.hero-photo{left:532px;top:0;width:668px;height:630px;background:linear-gradient(135deg,#e6e9ee 0%,#c7ccd3 45%,#6f7885 80%,#3d4450 100%)}
.topbar{top:12px;left:150px;display:flex;gap:8px}
.soc{width:18px;height:18px;border:1px solid #555;border-radius:50%}
.contact-top{top:11px;font-size:13px;display:flex;align-items:center;gap:6px}
.brand{left:152px;top:63px;font-size:19px;font-weight:700;color:var(--ink)}
.nav{top:65px;font-size:13px;font-weight:500}
.hero h1{left:152px;top:216px;font-size:51px;line-height:58px;font-weight:700;color:#333;letter-spacing:1px}
.hero p{left:152px;top:342px;font-size:15px;line-height:28px;color:#333;width:360px}

/* stats */
.stat{top:716px;width:219px;height:211px;color:var(--white);text-align:center}
.stat.navy{background:var(--navy)}
.stat.green{background:var(--green)}
.stat .ico{width:82px;height:82px;border-radius:50%;background:var(--white);margin:40px auto 12px;display:flex;align-items:center;justify-content:center}
.stat .ico div{width:64px;height:64px;border-radius:50%;border:1px solid #9aa;display:flex;align-items:center;justify-content:center}
.stat span{font-size:16px;line-height:20px;display:block}

/* insurance cards */
.card{width:248px;text-align:center}
.card.raised{background:var(--white);box-shadow:0 2px 14px rgba(0,0,0,.14)}
.card .icon{width:52px;height:52px;margin:20px auto 14px;border:1px solid var(--line);border-radius:4px;display:flex;align-items:center;justify-content:center}
.card h3{font-size:16px;font-weight:600;margin-bottom:10px}
.card h3.hl{color:var(--green)}
.card p{font-size:11px;line-height:19px;color:var(--muted);padding:0 22px}

/* about */
.about{top:1771px;height:600px;background:var(--bg-soft)}
.about p{font-size:11px;line-height:20px;color:#555;width:430px}

/* partners */
.partners{top:2371px;height:312px;background:linear-gradient(90deg,#2c5aa8,#3f6fb8 50%,#2d5ba5);overflow:hidden}
.logo-box{top:187px;width:186px;height:54px;background:var(--white);display:flex;align-items:center;justify-content:center;font-size:17px;font-weight:600;color:#222;letter-spacing:.5px}

/* testimonials */
.tcard{top:2909px;width:445px;height:225px;background:var(--white);box-shadow:0 2px 16px rgba(0,0,0,.1);text-align:center}
.tcard p{font-size:11px;line-height:22px;color:#555;padding:38px 28px 0}
.quote{top:-14px;left:16px;font-size:70px;line-height:70px;color:#c3cde0;font-family:Georgia,serif}
.person{display:flex;align-items:center;gap:14px;justify-content:center;margin-top:16px;margin-left:-40px}
.avatar{width:54px;height:54px;border-radius:50%;background:linear-gradient(#b9b2a8,#6e6358)}
.person h4{font-size:15px;font-weight:600;color:var(--navy);text-align:left}
.stars{color:#f4a21c;font-size:16px;letter-spacing:2px;text-align:left}
.arrow{width:32px;height:32px;border-radius:50%;display:flex;align-items:center;justify-content:center}
.dot{width:7px;height:7px;border-radius:50%;background:#c8ccd4}

/* contact */
.contact{top:3285px;height:615px;background:var(--bg-soft)}
.field{background:var(--white);border:1px solid var(--line);border-radius:3px;font-size:11px;color:#999;padding:12px 14px}

/* footer */
.cta{left:150px;top:3995px;width:918px;height:281px;background:var(--green-light);border-radius:14px;text-align:center;color:var(--white);z-index:2}
.footer{top:4134px;height:590px;background:var(--navy-deep);color:var(--white)}
.fcol{width:300px;text-align:center}
.fcol h5{font-size:13px;font-weight:600;margin:10px 0 14px}
.fcol p{font-size:12px;line-height:24px;color:#d7def0}
.fsoc{width:34px;height:34px;border-radius:50%;background:var(--white)}
</style>
</head>
<body>

<!-- header + hero -->
<header class="hero">
  <div class="abs hero-photo" role="img" aria-label="Photo of an insurance agent shaking hands with a client at an office table"></div>
  <div class="abs topbar"><span class="soc"></span><span class="soc"></span><span class="soc"></span><span class="soc"></span></div>
  <div class="abs contact-top" style="left:695px">
    <svg width="18" height="18" viewBox="0 0 24 24"><circle cx="12" cy="12" r="11" fill="none" stroke="#333"/><path d="M8 7l2 0 1 3-1.5 1a6 6 0 0 0 3 3l1-1.5 3 1v2c-4 1-9-4-8.5-8.5z" fill="#333"/></svg>
    (555) 014-2278
  </div>
  <div class="abs contact-top" style="left:836px">
    <svg width="18" height="18" viewBox="0 0 24 24"><circle cx="12" cy="12" r="11" fill="none" stroke="#333"/><rect x="6" y="8" width="12" height="8" fill="none" stroke="#333"/><path d="M6 8l6 5 6-5" fill="none" stroke="#333"/></svg>
    info@brellowcover.com
  </div>
  <div class="abs brand">BRELLOW COVER INSURANCE</div>
  <div class="abs nav" style="left:544px">Home</div>
  <div class="abs nav" style="left:611px">About Us</div>
  <div class="abs nav" style="left:699px">Insurance Types ⌵</div>
  <div class="abs nav" style="left:849px">Contact Us</div>
  <div class="abs btn navy" style="left:941px;top:53px;width:127px;height:41px">Get a Quote</div>
  <h1 class="abs">PROTECT WHAT<br>MATTERS MOST</h1>
  <p class="abs">Comprehensive insurance solutions for your home, vehicle, health, and loved ones</p>
  <div class="abs btn navy" style="left:151px;top:413px;width:126px;height:38px">Get a Quote</div>
</header>

<!-- stats -->
<div class="abs stat navy" style="left:152px"><div class="ico"><div><svg width="30" height="30" viewBox="0 0 24 24" fill="none" stroke="#0d2f7d" stroke-width="1.5"><rect x="5" y="3" width="12" height="17"/><path d="M8 8h6M8 11h6M8 14h4"/><circle cx="17" cy="17" r="3"/></svg></div></div><span>Insurance<br>Policies</span></div>
<div class="abs stat green" style="left:384px"><div class="ico"><div><svg width="32" height="32" viewBox="0 0 24 24" fill="none" stroke="#333" stroke-width="1.5"><circle cx="12" cy="12" r="9"/><circle cx="9" cy="10" r=".6" fill="#333"/><circle cx="15" cy="10" r=".6" fill="#333"/><path d="M8 14c2 3 6 3 8 0"/></svg></div></div><span>1000+ Happy<br>Clients</span></div>
<div class="abs stat navy" style="left:617px"><div class="ico"><div><svg width="32" height="32" viewBox="0 0 24 24" fill="none" stroke="#0d2f7d" stroke-width="1.5"><circle cx="12" cy="10" r="4"/><path d="M6 10a6 6 0 0 1 12 0M5 20c1-4 4-5 7-5s6 1 7 5"/></svg></div></div><span>Professional<br>Support</span></div>
<div class="abs stat green" style="left:850px"><div class="ico"><div><svg width="32" height="32" viewBox="0 0 24 24" fill="none" stroke="#333" stroke-width="1.5"><circle cx="12" cy="12" r="4"/><circle cx="12" cy="12" r="8" stroke-dasharray="3 2"/></svg></div></div><span>Free Lifetime<br>Updates</span></div>

<!-- insurance solutions -->
<div class="abs label center" style="top:1015px;text-align:center">Our Insurances</div>
<div class="abs title center" style="top:1042px;text-align:center">Our Various Insurance Solutions</div>
<div class="abs rule" style="left:568px;top:1087px"></div>

<div class="abs card raised" style="left:114px;top:1132px;height:226px">
  <div class="icon"><svg width="30" height="30" viewBox="0 0 24 24" fill="none" stroke="#0d2f7d" stroke-width="1.6"><path d="M3 11l9-7 9 7M5 10v10h14V10"/><circle cx="12" cy="14" r="2.5"/></svg></div>
  <h3 class="hl">Homeowners</h3><p>Protect your home and belongings from damage, theft, or disaster with comprehensive homeowners coverage.</p></div>
<div class="abs card" style="left:382px;top:1132px">
  <div class="icon"><svg width="30" height="30" viewBox="0 0 24 24" fill="#0d2f7d"><path d="M4 12l2-5h12l2 5v6H4z"/><circle cx="8" cy="15" r="1.4" fill="#fff"/><circle cx="16" cy="15" r="1.4" fill="#fff"/></svg></div>
  <h3>Auto Insurance</h3><p>Safeguard your vehicle against accidents, theft, or damage, ensuring you're covered on the road.</p></div>
<div class="abs card" style="left:630px;top:1132px">
  <div class="icon"><svg width="30" height="30" viewBox="0 0 24 24" fill="none" stroke="#0d2f7d" stroke-width="1.6"><path d="M3 10l9-6 9 6M5 10v10h14V10M9 20v-5h6v5"/></svg></div>
  <h3>Renters Insurance</h3><p>Protect personal belongings in a rental space, covering damage, theft, or loss due to disasters.</p></div>
<div class="abs card" style="left:876px;top:1132px">
  <div class="icon"><svg width="30" height="30" viewBox="0 0 24 24" fill="#0d2f7d"><rect x="6" y="3" width="12" height="18"/><g fill="#fff"><rect x="8" y="6" width="2" height="2"/><rect x="14" y="6" width="2" height="2"/><rect x="8" y="11" width="2" height="2"/><rect x="14" y="11" width="2" height="2"/></g></svg></div>
  <h3>Condo Insurance</h3><p>Cover your condo unit and personal property, filling the gap not covered by the building's insurance.</p></div>

<div class="abs card" style="left:93px;top:1381px">
  <div class="icon"><svg width="30" height="30" viewBox="0 0 24 24" fill="none" stroke="#0d2f7d" stroke-width="1.6"><path d="M5 11l7-6 7 6v5H5z"/><path d="M2 19c3-2 5 2 8 0s5 2 8 0 3 0 4 0"/></svg></div>
  <h3>Flood Insurance</h3><p>Provide financial protection against water damage caused by floods, which are often excluded from standard coverage.</p></div>
<div class="abs card" style="left:354px;top:1381px">
  <div class="icon"><svg width="30" height="30" viewBox="0 0 24 24" fill="none" stroke="#0d2f7d" stroke-width="1.8"><circle cx="11" cy="4" r="1.6"/><path d="M11 7v6h5l2 6M8 10a6 6 0 1 0 7 8"/></svg></div>
  <h3>Disability Insurance</h3><p>Receive income replacement if you're unable to work due to illness or injury, ensuring financial security.</p></div>
<div class="abs card" style="left:615px;top:1381px">
  <div class="icon"><svg width="30" height="30" viewBox="0 0 24 24"><path d="M12 21C4 15 2 11 4 7s7-3 8 0c1-3 6-4 8 0s0 8-8 14z" fill="#0d2f7d"/><path d="M12 9v6M9 12h6" stroke="#fff" stroke-width="1.8"/></svg></div>
  <h3>Life Insurance</h3><p>Protect your loved ones financially after your passing, covering funeral expenses and ongoing living costs.</p></div>
<div class="abs card" style="left:876px;top:1381px">
  <div class="icon"><svg width="30" height="30" viewBox="0 0 24 24"><path d="M12 2l8 3v7c0 5-4 8-8 10-4-2-8-5-8-10V5z" fill="#0d2f7d"/><circle cx="12" cy="12" r="4" fill="#fff"/><path d="M12 10v4M10 12h4" stroke="#0d2f7d" stroke-width="1.5"/></svg></div>
  <h3>Health Insurance</h3><p>Cover medical expenses, from check-ups to emergencies, ensuring you get the care you need without financial strain.</p></div>

<div class="abs btn green" style="left:543px;top:1639px;width:132px;height:40px">Explore All</div>

<!-- about -->
<section class="about">
  <div class="abs" style="left:150px;top:71px;width:294px;height:349px;background:linear-gradient(160deg,#8b7d6c,#c9b9a3 60%,#6d6456)" role="img" aria-label="Photo of an agent talking with a smiling couple at their front door"></div>
  <div class="abs" style="left:251px;top:308px;width:303px;height:220px;background:var(--white);padding:10px"><div style="width:100%;height:100%;background:radial-gradient(circle at 50% 55%,#f1ece6 0%,#d6b9a2 60%,#c49a80 100%)" role="img" aria-label="Photo of hands holding a small model house"></div></div>
  <div class="abs label" style="left:626px;top:98px">Who We Are</div>
  <div class="abs title" style="left:626px;top:125px;line-height:40px">About Brellow Cover<br>Insurance</div>
  <p class="abs" style="left:626px;top:248px">At Brellow Cover Insurance, we're dedicated to providing you with reliable, comprehensive insurance solutions tailored to your needs. Our mission is simple: to offer you peace of mind with the protection you deserve. We specialize in home, auto, health, and life insurance, and our experienced team is committed to helping you find the right coverage for every stage of life.</p>
  <p class="abs" style="left:626px;top:388px">Founded with a focus on customer satisfaction, Brellow Cover Insurance has grown to become a trusted partner in securing what matters most.</p>
  <div class="abs btn green" style="left:626px;top:462px;width:137px;height:40px">Learn More</div>
</section>

<!-- partners -->
<section class="partners" role="img" aria-label="Blue-tinted photo of smiling clients behind the partner list">
  <div class="abs label center" style="top:70px;text-align:center">Our Partners</div>
  <div class="abs center" style="top:100px;text-align:center;font-size:28px;font-weight:600;color:#fff">Trusted Partners for Your Protection</div>
  <div class="abs rule" style="left:568px;top:143px"></div>
  <div class="abs logo-box" style="left:-62px">Varnix</div>
  <div class="abs logo-box" style="left:169px">Ostle</div>
  <div class="abs logo-box" style="left:401px">Meridale Mutual</div>
  <div class="abs logo-box" style="left:633px">Quillor</div>
  <div class="abs logo-box" style="left:863px">Dunmarrow</div>
  <div class="abs logo-box" style="left:1094px;justify-content:flex-start;padding-left:40px">Pellwick</div>
</section>

<!-- testimonials -->
<div class="abs label center" style="top:2777px;text-align:center">Clients Testimonials</div>
<div class="abs title center" style="top:2803px;text-align:center">Proven Success Stories</div>
<div class="abs rule" style="left:568px;top:2849px"></div>
<div class="abs tcard" style="left:150px"><div class="abs quote">“</div>
  <p>It is a long established fact that a reader will be distracted by the readable content of a page when looking at its layout. The point of using Lorem Ipsum is that it has a more-or-less normal distribution of letters, as opposed to using 'Content here, content here'.</p>
  <div class="person"><div class="avatar" role="img" aria-label="Client portrait"></div><div><h4>Dalen Whitcombe</h4><div class="stars">★★★★★</div></div></div></div>
<div class="abs tcard" style="left:624px"><div class="abs quote">“</div>
  <p>It is a long established fact that a reader will be distracted by the readable content of a page when looking at its layout. The point of using Lorem Ipsum is that it has a more-or-less normal distribution of letters, as opposed to using 'Content here, content here'.</p>
  <div class="person"><div class="avatar" role="img" aria-label="Client portrait"></div><div><h4>Orrin Halvard</h4><div class="stars">★★★★★</div></div></div></div>
<div class="abs arrow" style="left:134px;top:3004px;background:#fff;box-shadow:0 1px 6px rgba(0,0,0,.15)"><svg width="14" height="14" viewBox="0 0 24 24" fill="none" stroke="#8bc34a" stroke-width="2.5"><path d="M20 12H5M11 6l-6 6 6 6"/></svg></div>
<div class="abs arrow" style="left:1052px;top:3004px;background:var(--green-light)"><svg width="14" height="14" viewBox="0 0 24 24" fill="none" stroke="#fff" stroke-width="2.5"><path d="M4 12h15M13 6l6 6-6 6"/></svg></div>
<div class="abs" style="left:565px;top:3179px;display:flex;gap:12px;align-items:center"><span class="dot"></span><span class="dot"></span><span class="dot" style="width:14px;height:14px;background:var(--navy)"></span><span class="dot"></span><span class="dot"></span></div>

<!-- contact -->
<section class="contact">
  <div class="abs label" style="left:150px;top:86px">Contact Us</div>
  <div class="abs title" style="left:150px;top:113px">Get in Touch with Us</div>
  <div class="abs rule" style="left:150px;top:158px"></div>
  <div class="abs field" style="left:150px;top:203px;width:228px;height:40px">First Name</div>
  <div class="abs field" style="left:398px;top:203px;width:226px;height:40px">Last Name</div>
  <div class="abs field" style="left:150px;top:266px;width:228px;height:40px">Email</div>
  <div class="abs field" style="left:398px;top:266px;width:226px;height:40px">Phone</div>
  <div class="abs field" style="left:150px;top:328px;width:474px;height:118px">Message</div>
  <div class="abs btn green" style="left:150px;top:492px;width:147px;height:40px">Submit Now</div>
  <div class="abs" style="left:690px;top:73px;width:378px;height:473px;border-radius:12px;background:linear-gradient(160deg,#cfd6dc,#8f9aa3 55%,#3a3f45)" role="img" aria-label="Photo of an agent reviewing a policy document with a client"></div>
</section>

<!-- call to action -->
<div class="abs cta">
  <div style="margin-top:52px;font-size:29px;font-weight:600">Secure a Future with Customized Quote Today!</div>
  <div style="margin:18px auto 0;width:700px;font-size:12px;line-height:22px;font-weight:500">Protect what matters most with tailored insurance solutions. Get a personalized quote today and secure peace of mind.</div>
  <div class="btn" style="margin:34px auto 0;width:213px;height:41px;background:#fff;color:var(--navy);font-size:13px;font-weight:600">Get a Quote</div>
</div>

<!-- footer -->
<footer class="footer">
  <div class="abs" style="left:150px;top:240px;display:flex;align-items:center;gap:8px">
    <span style="width:12px;height:12px;background:var(--green-light)"></span>
    <span style="font-size:14px;font-weight:600">BRELLOW COVER</span>
  </div>
  <p class="abs" style="left:352px;top:230px;width:510px;font-size:11px;line-height:21px;color:#d7def0">Brellow Cover Insurance, we're dedicated to providing you with reliable, comprehensive insurance solutions tailored to your needs.</p>
  <div class="abs" style="left:934px;top:229px;display:flex;gap:16px"><span class="fsoc"></span><span class="fsoc" style="background:var(--green-light)"></span><span class="fsoc"></span></div>
  <div class="abs" style="left:150px;top:281px;width:918px;height:1px;background:#3a63a8"></div>
  <div class="abs center" style="top:318px;text-align:center;font-size:17px;font-weight:500">Contact Information</div>
  <div class="abs fcol" style="left:140px;top:364px">
    <svg width="22" height="22" viewBox="0 0 24 24"><path d="M5 3h4l2 5-2.5 1.5a11 11 0 0 0 6 6L16 13l5 2v4c-9 1-17-7-16-16z" fill="#8bc34a"/></svg>
    <h5>Call Us</h5><p>(555) 019-3346</p></div>
  <div class="abs" style="left:407px;top:364px;width:1px;height:120px;background:#3a63a8"></div>
  <div class="abs fcol" style="left:446px;top:364px">
    <svg width="22" height="22" viewBox="0 0 24 24"><path d="M12 2a7 7 0 0 0-7 7c0 5 7 13 7 13s7-8 7-13a7 7 0 0 0-7-7z" fill="#8bc34a"/><circle cx="12" cy="9" r="2.5" fill="#0b3b8c"/></svg>
    <h5>Find Us</h5><p>123, Lorem Ipsum is simply dummy<br>text of the printing</p></div>
  <div class="abs" style="left:784px;top:364px;width:1px;height:120px;background:#3a63a8"></div>
  <div class="abs fcol" style="left:778px;top:364px">
    <svg width="24" height="22" viewBox="0 0 24 24"><rect x="2" y="5" width="20" height="14" fill="#8bc34a"/><path d="M2 5l10 8 10-8" fill="none" stroke="#0b3b8c" stroke-width="1.5"/></svg>
    <h5>Email Address</h5><p>hello@brellowcover.com</p></div>
  <div class="abs" style="left:150px;top:508px;width:918px;height:1px;background:#3a63a8"></div>
  <div class="abs" style="left:150px;top:546px;font-size:12px">Copyright © 2025 Brellow Cover Insurance - All Rights Reserved.</div>
  <div class="abs" style="left:871px;top:546px;font-size:12px">Terms of use</div>
  <div class="abs" style="left:983px;top:546px;font-size:12px">Privacy Policy</div>
</footer>

</body>
</html>
```